business card - Helicopter Flight Services, Flight School, etc.

We need a business card design for a new helicopter service.

We offer Helicopter Flight Services, Aerial Filming & Photography, Flight School, and Helicopter Tours. In that order.

Summit BladeAir, Inc.
Dennis Tollerby
SummitBladeair@Kestmail.com
626-418-7352

Based at the Brenwick Airport in Van Nuys, CA. The final design should communicate integrity and safety. Pictures or logos at your discretion.

Card back side - surprise me.

```html
<!DOCTYPE html>
<html lang="en">
<head>
<meta charset="utf-8">
<title>Summit BladeAir, Inc. – Business Card</title>
<link href="https://fonts.googleapis.com/css2?family=Open+Sans:wght@300;400;700&display=swap" rel="stylesheet">
<style>
  :root {
    --page-bg: #e9ebee;
    --card-white: #ffffff;
    --brand-blue: #1f6fc0;
    --brand-blue-light: #3a93d6;
    --text-muted: #5a9fd8;
    --divider: #cfd9e4;
    --back-top: #3ba3dd;
    --back-bottom: #0d4fa3;
    --back-text: #ffffff;
  }
  * { box-sizing: border-box; margin: 0; padding: 0; }
  html, body {
    width: 1200px; height: 913px; overflow: hidden;
    background: var(--page-bg);
    font-family: "Open Sans", Arial, sans-serif;
  }
  .canvas { position: relative; width: 1200px; height: 913px; }
  .card {
    position: absolute; width: 560px; height: 320px;
    border-radius: 4px;
    box-shadow: 0 6px 18px rgba(0,0,0,0.18);
  }
  .card-front { left: 70px; top: 110px; background: var(--card-white); }
  .card-back {
    left: 570px; top: 480px;
    background: linear-gradient(160deg, var(--back-top) 0%, var(--brand-blue) 55%, var(--back-bottom) 100%);
  }

  /* front */
  .brand {
    position: absolute; left: 28px; top: 146px;
    width: 262px;
    display: flex; align-items: center; gap: 8px;
    white-space: nowrap;
  }
  .brand-dot {
    width: 12px; height: 12px; border-radius: 50%;
    background: var(--brand-blue); flex: none;
  }
  .brand-name {
    font-weight: 700; font-size: 16px; letter-spacing: 0;
    color: var(--brand-blue); text-transform: uppercase;
  }
  .divider {
    position: absolute; left: 304px; top: 110px;
    width: 1px; height: 100px; background: var(--divider);
  }
  .contact { position: absolute; left: 322px; top: 112px; }
  .contact-name { font-weight: 700; font-size: 20px; color: var(--brand-blue); }
  .contact-role { font-weight: 400; font-size: 12px; color: var(--text-muted); margin-top: 1px; }
  .contact-line {
    display: flex; align-items: center; gap: 6px;
    font-size: 12.5px; color: var(--brand-blue-light); margin-top: 8px;
    white-space: nowrap;
  }
  .contact-line + .contact-line { margin-top: 4px; }
  .contact-line svg { width: 11px; height: 11px; flex: none; }

  /* back */
  .back-brand {
    position: absolute; left: 40px; top: 200px;
    display: flex; align-items: center; gap: 10px;
    white-space: nowrap;
  }
  .back-brand .brand-dot { background: var(--back-text); width: 16px; height: 16px; }
  .back-brand .brand-name { color: var(--back-text); font-size: 22px; }
  .services {
    position: absolute; right: 40px; top: 56px;
    list-style: none; color: var(--back-text);
    font-size: 14px; line-height: 1.45; font-weight: 400;
    white-space: nowrap;
  }
</style>
</head>
<body>
<div class="canvas">
  <section class="card card-front" aria-label="Card front">
    <div class="brand">
      <span class="brand-dot"></span>
      <span class="brand-name">Summit BladeAir, Inc.</span>
    </div>
    <div class="divider"></div>
    <div class="contact">
      <div class="contact-name">Dennis Tollerby</div>
      <div class="contact-role">Owner</div>
      <div class="contact-line">
        <svg viewBox="0 0 12 12" aria-hidden="true"><path d="M2.5 1h2l1 2.5-1.3 1a6 6 0 0 0 3.3 3.3l1-1.3L11 7.5v2A1.5 1.5 0 0 1 9.5 11 8.5 8.5 0 0 1 1 2.5 1.5 1.5 0 0 1 2.5 1z" fill="none" stroke="currentColor" stroke-width="1.1"/></svg>
        <span>626-418-7352</span>
      </div>
      <div class="contact-line">
        <svg viewBox="0 0 12 12" aria-hidden="true"><rect x="1" y="2.5" width="10" height="7" rx="0.8" fill="none" stroke="currentColor" stroke-width="1.1"/><path d="M1.3 3l4.7 3.6L10.7 3" fill="none" stroke="currentColor" stroke-width="1.1"/></svg>
        <span>SummitBladeair@Kestmail.com</span>
      </div>
    </div>
  </section>

  <section class="card card-back" aria-label="Card back">
    <ul class="services">
      <li>Aerial Filming &amp; Photography</li>
      <li>Flight School</li>
      <li>Helicopter Tours (In that order)</li>
    </ul>
    <div class="back-brand">
      <span class="brand-dot"></span>
      <span class="brand-name">Summit BladeAir, Inc.</span>
    </div>
  </section>
</div>
</body>
</html>
```